Copper Field Agency Website - Wordpress Web UPDATED BRIEF

FINAL LOGO UPLOADED - please look to this as reference for how we would like the site to look and feel.

We are a digital marketing agency - looking to have a new website built. We are looking for a simple one page feel of site that will allow us to grow it later. (Feel free to take some liberties with that if your imagination veers off) Must be very, playful, bold, sleek and easily integrate video. Wordpress only.

Overview:

Copper Field is a creative constellation. We are built on what's great about the shared economy. With access to thousands of content creators, designers, technicians, writers, strategists and other creatives around the world, we are built differently than a traditional “brick and mortar” Marketing Agency. We provide the traditional services our clients have come to expect, without the “5X factor” of covering the overhead common in the old agency model. We believe even better work can be created in collaboration with our clients and by passing those savings back to them for their use. Our clients pay for our art, our work and our passion –not our furniture.

"Copper Field, Let's Build Together"

Target Market(s)

companies looking for creative agency help, video production, creative consulting and coaching

Industry/Entity Type

Digital Marketing

Coding

Coded - Design and coding required

Number of Pages Required

1 page

Font styles to use
Sans Serif

Colors
3277b5
33a6d7
ec1f27

Requirements
Must have
• Wordpress design is a must. Looking for a one sheet homepage - with sections that are all on the main front page. We will have videos to embed, and should be able to have client logos and easy access to show a variety of our creative work.
• Please look to the logo for how we would like the site to feel.
• Please think "icon process flow" instead of blocks of text (which we used to have). Use the text to explain what the process flow should represent - don't actually copy paste the text but show it visually in icons.
Nice to have
• innovation around how we show video content. solid colors complementary to our palette and aesthetic.
Should not have
• Standard HTML coding

```html
<!DOCTYPE html>
<html lang="en">
<head>
<meta charset="utf-8">
<title>Copper Field Agency</title>
<link href="https://fonts.googleapis.com/css2?family=Lato:wght@400;700;900&display=swap" rel="stylesheet">
<style>
:root{
  --navy:#1d3c78;
  --navy-deep:#14295a;
  --blue:#3277b5;
  --sky:#33a6d7;
  --red:#ec1f27;
  --red-deep:#c3161f;
  --ink:#222;
  --muted:#666;
  --soft:#efefef;
  --ghost:#e4e4e4;
  --black:#101010;
  --white:#fff;
}
*{box-sizing:border-box;margin:0;padding:0}
html,body{width:1200px;height:4536px;overflow:hidden}
body{position:relative;font-family:'Lato',sans-serif;color:var(--ink);background:var(--white)}
.abs{position:absolute}
a{color:inherit;text-decoration:none}

/* top bar */
.topbar{top:0;left:0;width:1200px;height:56px;background:var(--white);font-size:15px;color:#333}
.topbar .item{position:absolute;top:18px;display:flex;align-items:center;gap:8px}
.topbar .dot{width:14px;height:14px;border-radius:3px;background:var(--navy)}
.topbar .social{position:absolute;top:20px;display:flex;gap:14px;left:1020px}
.topbar .social span{width:16px;height:16px;border-radius:50%;background:var(--navy)}

/* hero */
.hero{top:56px;left:0;width:1200px;height:780px;background:linear-gradient(135deg,#6e2a1f 0%,#9c3c28 40%,#7a2e22 70%,#4f1e18 100%)}
.nav{top:56px;left:0;width:1200px;height:36px;background:var(--navy);color:var(--white);font-size:14px;font-weight:700;letter-spacing:.5px}
.nav ul{list-style:none;position:absolute;top:10px;display:flex;gap:34px}
.brand{top:0;left:500px;width:200px;height:170px;display:flex;flex-direction:column;align-items:center;justify-content:flex-end;padding-bottom:14px;background:var(--navy);border-radius:0 0 100px 100px}
.brand .mark{width:70px;height:70px;border-radius:50%;background:var(--red);margin-bottom:12px}
.brand .name{color:var(--white);font-weight:900;font-size:24px;letter-spacing:1px}

/* section headings */
.ghost{font-weight:900;color:var(--ghost);letter-spacing:4px;text-align:center;width:1200px;left:0}
.title{font-weight:900;color:#111;text-align:center;width:1200px;left:0;font-size:46px;letter-spacing:1px}

/* about */
.about-photo{top:840px;left:196px;width:330px;height:330px;border-radius:50%;border:10px solid var(--blue);background:linear-gradient(180deg,#3a8fe0 0%,#6fb4ef 55%,#b0553a 56%,#8c3c2a 100%)}
.about-ghost{top:812px;left:612px;font-size:100px;font-weight:900;color:var(--ghost);letter-spacing:4px}
.about-title{top:866px;left:616px;font-size:48px;font-weight:900;color:#111}
.about-text{top:940px;left:620px;width:540px;font-size:15px;line-height:1.85;color:var(--muted)}

/* services */
.services-bg{top:0;left:0}
.flow{top:1700px;left:40px;width:1120px;height:420px}
.flow-label{position:absolute;font-size:19px;font-weight:700;color:#222;width:200px;text-align:center}

/* clients */
.clients{top:2505px;left:80px;width:1040px;display:flex;justify-content:space-between;align-items:center}
.client{display:flex;align-items:center;gap:10px;font-size:26px;font-weight:700;color:#555}
.client .sq{width:26px;height:26px;background:#555}
.client .ci{width:28px;height:28px;border-radius:50%;background:#555}

/* testimonials */
.card{top:2950px;width:300px;height:300px;background:var(--white);border-radius:6px;text-align:center;padding:96px 26px 0}
.avatar{position:absolute;top:-36px;left:100px;width:100px;height:100px;border-radius:50%;border:5px solid var(--white);background:linear-gradient(180deg,#c59a7c,#7b5a48)}
.card h3{font-size:22px;font-weight:700;color:#222;margin-bottom:14px}
.card p{font-size:14px;line-height:1.7;color:#888;font-style:italic}
.arrow{top:3080px;width:20px;height:34px}

/* gallery */
.work{top:3592px;height:244px}

/* footer */
.footer{top:3900px;left:0;width:1200px;height:636px;background:var(--black);color:var(--white)}
.news-title{top:172px;left:120px;font-size:32px;font-weight:400}
.news-input{top:176px;left:536px;width:400px;height:44px;background:var(--white);color:#999;font-size:13px;padding:14px 16px}
.news-btn{top:176px;left:936px;width:124px;height:44px;background:var(--navy);font-size:16px;font-weight:700;display:flex;align-items:center;justify-content:center}
.col{top:280px;font-size:14px;line-height:1.75;color:#ccc}
.col h4{font-size:16px;font-weight:700;color:var(--white);letter-spacing:1px;margin-bottom:12px}
.foot-social{top:544px;left:522px;display:flex;gap:16px}
.foot-social span{width:32px;height:32px;border-radius:50%;background:var(--blue)}
.legal{top:586px;left:0;width:1200px;text-align:center;font-size:13px;color:#bbb}
</style>
</head>
<body>

<!-- top bar -->
<header class="abs topbar">
  <div class="item" style="left:120px"><span class="dot"></span>+1 555 014 7820</div>
  <div class="item" style="left:338px"><span class="dot"></span>info@copperfield.example</div>
  <div class="item" style="left:820px">Log in</div>
  <div class="item" style="left:920px">Sign Up</div>
  <div class="social"><span></span><span></span><span></span><span></span></div>
</header>

<!-- hero -->
<section class="abs hero" role="img" aria-label="Photo of a brick wall office desk with a monitor showing a video call, cactus plants and a pencil cup"></section>
<nav class="abs nav">
  <ul style="left:80px"><li>HOME</li><li>ABOUT US</li><li>SERVICES</li><li>OUR CLIENTS</li></ul>
  <ul style="left:764px"><li>TESTIMONIALS</li><li>GALLERY</li><li>CONTACT US</li></ul>
</nav>
<div class="abs brand"><span class="mark"></span><span class="name">COPPER FIELD</span></div>

<svg class="abs" style="top:0;left:0" width="1200" height="4536" aria-hidden="true">
  <!-- hero slant -->
  <polygon points="0,836 1200,744 1200,860 0,860" fill="#fff"/>
  <!-- services band -->
  <polygon points="0,1410 1200,1440 1200,2180 0,2200" fill="#efefef"/>
  <polygon points="0,1360 560,1440 0,1470" fill="var(--navy)"/>
  <polygon points="760,1440 1200,1384 1200,1450" fill="var(--navy-deep)"/>
  <polygon points="0,2150 500,2200 0,2230" fill="var(--navy)"/>
  <polygon points="700,2200 1200,2140 1200,2236" fill="var(--blue)"/>
  <!-- testimonials band -->
  <defs>
    <linearGradient id="testiGrad" x1="0" y1="0" x2="0" y2="1">
      <stop offset="0" stop-color="#1d3c78"/>
      <stop offset="0.55" stop-color="#5a2a5e"/>
      <stop offset="1" stop-color="#d01f2c"/>
    </linearGradient>
  </defs>
  <polygon points="0,2700 1200,2650 1200,3260 0,3310" fill="url(#testiGrad)"/>
  <polygon points="0,2680 420,2660 0,2720" fill="var(--navy)"/>
  <polygon points="760,3290 1200,3240 1200,3320" fill="var(--red)"/>
</svg>

<!-- about -->
<section>
  <div class="abs about-photo" role="img" aria-label="Photo of a bricklayer working on top of a chimney against a blue sky"></div>
  <div class="abs about-ghost">ABOUT US</div>
  <h2 class="abs about-title">ABOUT US</h2>
  <p class="abs about-text">Copper Field is a creative constellation. We are built on what's great about the shared economy. With access to thousands of content creators, designers, technicians, writers, strategists and other creatives around the world, we are built differently than a traditional “brick and mortar” Marketing Agency. We provide the traditional services our clients have come to expect, without the “5X factor” of covering the overhead common in the old agency model. We believe even better work can be created in collaboration with our clients and by passing those savings back to them for their use. Our clients pay for our art, our work and our passion – not our furniture.</p>
</section>

<!-- services -->
<section>
  <div class="abs ghost" style="top:1536px;font-size:96px">SERVICES</div>
  <h2 class="abs title" style="top:1598px">SERVICES</h2>
  <svg class="abs flow" viewBox="0 0 1120 420" aria-hidden="true">
    <line x1="20" y1="64" x2="1100" y2="64" stroke="#333" stroke-width="3"/>
    <g fill="none" stroke-width="3">
      <!-- nodes: x centres -->
      <g transform="translate(70,64)">
        <circle r="54" fill="#fff" stroke="var(--navy)" stroke-width="8"/>
        <circle cx="-4" cy="-4" r="14" stroke="var(--navy)"/><line x1="6" y1="6" x2="18" y2="18" stroke="var(--red)"/>
        <line x1="0" y1="60" x2="0" y2="150" stroke="var(--navy)"/><circle cy="156" r="6" fill="var(--navy)" stroke="none"/>
      </g>
      <g transform="translate(210,64)">
        <circle r="54" fill="#fff" stroke="var(--red)" stroke-width="8"/>
        <circle r="18" stroke="var(--navy)"/><circle r="8" stroke="var(--red)"/><circle r="2" fill="var(--red)"/>
        <line x1="0" y1="60" x2="0" y2="226" stroke="var(--red)"/><circle cy="232" r="6" fill="var(--red)" stroke="none"/>
      </g>
      <g transform="translate(350,64)">
        <circle r="54" fill="#fff" stroke="var(--navy)" stroke-width="8"/>
        <rect x="-14" y="-18" width="28" height="36" rx="3" stroke="var(--navy)"/><line x1="-7" y1="-6" x2="7" y2="-6" stroke="var(--red)"/><line x1="-7" y1="4" x2="7" y2="4" stroke="var(--red)"/>
        <line x1="0" y1="60" x2="0" y2="150" stroke="var(--navy)"/><circle cy="156" r="6" fill="var(--navy)" stroke="none"/>
      </g>
      <g transform="translate(490,64)">
        <circle r="54" fill="#fff" stroke="var(--navy)" stroke-width="8"/>
        <rect x="-18" y="-14" width="36" height="26" rx="3" stroke="var(--navy)"/><polygon points="-5,-7 8,-1 -5,5" fill="var(--red)" stroke="none"/>
        <line x1="0" y1="60" x2="0" y2="226" stroke="var(--navy)"/><circle cy="232" r="6" fill="var(--navy)" stroke="none"/>
      </g>
      <g transform="translate(630,64)">
        <circle r="54" fill="#fff" stroke="var(--navy)" stroke-width="8"/>
        <rect x="-18" y="-12" width="36" height="24" rx="3" stroke="var(--navy)"/><circle r="6" stroke="var(--red)"/>
        <line x1="0" y1="60" x2="0" y2="150" stroke="var(--navy)"/><circle cy="156" r="6" fill="var(--navy)" stroke="none"/>
      </g>
      <g transform="translate(770,64)">
        <circle r="54" fill="#fff" stroke="var(--red)" stroke-width="8"/>
        <line x1="-14" y1="14" x2="-14" y2="2" stroke="var(--navy)"/><line x1="0" y1="14" x2="0" y2="-6" stroke="var(--navy)"/><line x1="14" y1="14" x2="14" y2="-14" stroke="var(--red)"/>
        <line x1="0" y1="60" x2="0" y2="226" stroke="var(--red)"/><circle cy="232" r="6" fill="var(--red)" stroke="none"/>
      </g>
      <g transform="translate(910,64)">
        <circle r="54" fill="#fff" stroke="var(--navy)" stroke-width="8"/>
        <rect x="-18" y="-14" width="36" height="24" rx="3" stroke="var(--navy)"/><line x1="-8" y1="16" x2="8" y2="16" stroke="var(--red)"/>
        <line x1="0" y1="60" x2="0" y2="150" stroke="var(--navy)"/><circle cy="156" r="6" fill="var(--navy)" stroke="none"/>
      </g>
      <g transform="translate(1050,64)">
        <circle r="54" fill="#fff" stroke="var(--navy)" stroke-width="8"/>
        <polyline points="-16,10 -4,-2 4,6 16,-10" stroke="var(--red)"/><line x1="-18" y1="16" x2="18" y2="16" stroke="var(--navy)"/>
        <line x1="0" y1="60" x2="0" y2="150" stroke="var(--navy)"/><circle cy="156" r="6" fill="var(--navy)" stroke="none"/>
      </g>
    </g>
  </svg>
  <div class="abs" style="top:1700px;left:40px;width:1120px;height:420px">
    <span class="flow-label" style="left:-30px;top:236px">Discovery</span>
    <span class="flow-label" style="left:110px;top:312px">Strategy</span>
    <span class="flow-label" style="left:250px;top:236px">Project Management</span>
    <span class="flow-label" style="left:390px;top:312px">Content</span>
    <span class="flow-label" style="left:530px;top:236px">Production</span>
    <span class="flow-label" style="left:670px;top:312px">Paid Media</span>
    <span class="flow-label" style="left:950px;top:236px">Coaching</span>
  </div>
</section>

<!-- clients -->
<section>
  <div class="abs ghost" style="top:2300px;font-size:96px">CLIENTS</div>
  <h2 class="abs title" style="top:2370px">OUR CLIENTS</h2>
  <div class="abs clients">
    <span class="client">Maple Creative</span>
    <span class="client"><span class="sq"></span>SwiftPass</span>
    <span class="client"><span class="ci"></span>Northway Solutions</span>
    <span class="client">Bright Client</span>
    <span class="client"><span class="ci"></span>Linkora</span>
  </div>
</section>

<!-- testimonials -->
<section>
  <div class="abs ghost" style="top:2786px;font-size:96px;color:rgba(255,255,255,.14)">TESTIMONIALS</div>
  <h2 class="abs title" style="top:2852px;color:#fff;font-size:42px">WHAT OUR CUSTOMER SAY'S</h2>
  <svg class="abs arrow" style="left:14px" viewBox="0 0 20 34" aria-hidden="true"><polyline points="16,4 4,17 16,30" fill="none" stroke="#fff" stroke-width="4"/></svg>
  <svg class="abs arrow" style="left:1166px" viewBox="0 0 20 34" aria-hidden="true"><polyline points="4,4 16,17 4,30" fill="none" stroke="#fff" stroke-width="4"/></svg>
  <article class="abs card" style="left:120px">
    <div class="avatar" role="img" aria-label="Portrait photo of the client"></div>
    <h3>Thomas Ellery</h3>
    <p>Working with this team felt easy from day one. They listened closely, moved fast and delivered a campaign that our whole company is proud to share.</p>
  </article>
  <article class="abs card" style="left:450px">
    <div class="avatar" role="img" aria-label="Portrait photo of the client"></div>
    <h3>Owen Hartley</h3>
    <p>Clear ideas, honest pricing and great video work. Our launch reached more people than we hoped and the process stayed simple the whole way through.</p>
  </article>
  <article class="abs card" style="left:780px">
    <div class="avatar" role="img" aria-label="Portrait photo of the client"></div>
    <h3>Clara Benning</h3>
    <p>The coaching sessions gave our team new confidence. Every step was planned with care and the results keep growing month after month for us.</p>
  </article>
</section>

<!-- gallery -->
<section>
  <div class="abs ghost" style="top:3440px;font-size:96px">GALLERY</div>
  <h2 class="abs title" style="top:3508px;font-size:44px">OUR CREATIVE WORK</h2>
  <div class="abs work" style="left:88px;width:312px;background:linear-gradient(160deg,#c9c4bd,#8a6a52)" role="img" aria-label="Photo of a builder laying bricks on a wall"></div>
  <div class="abs work" style="left:432px;width:328px;background:linear-gradient(160deg,#b9b6b0,#7d7a75)" role="img" aria-label="Photo of stacked grey concrete blocks"></div>
  <div class="abs work" style="left:780px;width:332px;background:linear-gradient(160deg,#d4794c,#9a3f22)" role="img" aria-label="Photo of hollow clay bricks stacked together"></div>
</section>

<!-- footer -->
<footer class="abs footer">
  <h3 class="abs news-title">Subscribe Our Newsletter</h3>
  <div class="abs news-input">Your Email Here</div>
  <div class="abs news-btn">Subscribe</div>
  <div class="abs col" style="left:120px"><h4>QUICK LINKS</h4>Home<br>About Us<br>Services<br>Our Clients<br>Testimonials<br>Gallery<br>Contact Us</div>
  <div class="abs col" style="left:380px"><h4>IMPORTANT</h4>Login<br>FAQ<br>Privacy Policy</div>
  <div class="abs col" style="left:640px"><h4>CONTACT US</h4>PO Box 40218, Riverton, OH 45001<br>(555) 013-4472<br>info@copperfield.example</div>
  <div class="abs col" style="left:1000px"><h4>ACCOUNT</h4>Sign Up<br>Log in</div>
  <div class="abs foot-social"><span></span><span></span><span></span><span></span></div>
  <p class="abs legal">© 2019 Copper Field Agency. All Rights Reserved</p>
</footer>

</body>
</html>
```